Option Sheet

We need a one page option sheet with a left to right reading of the five options. It should be a one sheet, multiple colors and definitive separations between options This is used in a sales consultation. Backround or colors not in option need to have the follow RGB value (5 red, 20 green, 63 blue)

We added a smaller text file, please change that point

Target Market(s)

Divorce

Industry/Entity Type

Legal

Requirements
Must have
• 1) All five options left to right
• 2)language included in sheet

```html
<!DOCTYPE html>
<html lang="en">
<head>
<meta charset="utf-8">
<title>Five Options – Divorce</title>
<link rel="stylesheet" href="https://fonts.googleapis.com/css2?family=Titillium+Web:wght@600;700&family=Source+Sans+3:ital,wght@0,400;1,300&family=Montserrat:wght@500;700&display=swap">
<style>
  :root {
    --navy: rgb(5, 20, 63);
    --white: #ffffff;
    --ink: #3c3c44;
    --muted: #7a7a82;
    --rule: #ececef;
    --opt-nothing: #f4511e;
    --opt-counsel: #d9479b;
    --opt-diy: #4a3a9c;
    --opt-limited: #7ac522;
    --opt-hire: #17923f;
  }
  * { box-sizing: border-box; margin: 0; padding: 0; }
  html, body { width: 1200px; height: 680px; overflow: hidden; }
  body {
    background: var(--navy);
    position: relative;
    font-family: "Source Sans 3", "Helvetica Neue", Arial, sans-serif;
  }
  .sheet-title {
    position: absolute; left: 0; right: 0; top: 26px;
    text-align: center; color: var(--white);
    font-family: "Montserrat", Arial, sans-serif;
  }
  .sheet-title .kicker { display: block; font-size: 27px; font-weight: 500; letter-spacing: 1px; line-height: 34px; }
  .sheet-title .topic { display: block; font-size: 60px; font-weight: 700; letter-spacing: 2px; line-height: 72px; margin-top: -2px; }

  .option {
    position: absolute; top: 158px; width: 230px;
    background: var(--white);
    --accent: var(--ink);
  }
  .option--nothing { left: 16px;  height: 386px; --accent: var(--opt-nothing); }
  .option--counsel { left: 251px; height: 445px; --accent: var(--opt-counsel); }
  .option--diy     { left: 485px; height: 472px; --accent: var(--opt-diy); }
  .option--limited { left: 719px; height: 489px; --accent: var(--opt-limited); }
  .option--hire    { left: 954px; height: 505px; --accent: var(--opt-hire); }

  .option-head {
    height: 81px; margin: 0 5px;
    display: flex; flex-direction: column; align-items: center; justify-content: center;
    border-bottom: 1px solid var(--accent);
    padding-bottom: 4px;
  }
  .option-num { font-style: italic; font-weight: 300; font-size: 12.5px; color: var(--muted); line-height: 14px; }
  .option-name {
    font-family: "Titillium Web", Arial, sans-serif; font-weight: 700;
    color: var(--accent); font-size: 28px; line-height: 28px; text-align: center; letter-spacing: -0.3px;
  }
  .option--limited .option-name { font-size: 27px; line-height: 22px; margin-top: 2px; }
  .option--limited .option-head { justify-content: flex-end; padding-bottom: 9px; }

  .pros, .cons { padding: 16px 12px 0 20px; }
  .pros { min-height: 124px; border-bottom: 1px solid var(--rule); margin: 0 10px 0 0; padding-bottom: 8px; }
  .cons { padding-top: 22px; }
  .group-title { font-size: 17px; font-weight: 400; color: var(--ink); line-height: 22px; margin-bottom: 6px; }

  .points { list-style: none; }
  .points li {
    position: relative; padding-left: 27px;
    font-style: italic; font-weight: 300; font-size: 14.5px; line-height: 15px;
    color: #56565e; margin-bottom: 15px;
  }
  .points li::before {
    content: ""; position: absolute; left: 3px; top: 3px;
    width: 10px; height: 10px; border-radius: 50%; background: var(--accent);
  }
</style>
</head>
<body>
  <header class="sheet-title">
    <span class="kicker">Five Options</span>
    <span class="topic">DIVORCE</span>
  </header>

  <section class="option option--nothing">
    <div class="option-head">
      <span class="option-num">option #1</span>
      <h2 class="option-name">Do Nothing</h2>
    </div>
    <div class="pros">
      <h3 class="group-title">Advantages:</h3>
      <ul class="points">
        <li>Stay married</li>
        <li>No life Changes</li>
      </ul>
    </div>
    <div class="cons">
      <h3 class="group-title">Disadvantages:</h3>
      <ul class="points">
        <li>Remain unhappy, depressed, anxious</li>
        <li>Money and assets may disappear</li>
        <li>What is going to change?</li>
      </ul>
    </div>
  </section>

  <section class="option option--counsel">
    <div class="option-head">
      <span class="option-num">option #2</span>
      <h2 class="option-name">Go to Counseling</h2>
    </div>
    <div class="pros">
      <h3 class="group-title">Advantages:</h3>
      <ul class="points">
        <li>Reconcile marriage</li>
        <li>Help make a better life</li>
      </ul>
    </div>
    <div class="cons">
      <h3 class="group-title">Disadvantages:</h3>
      <ul class="points">
        <li>Past issues are highlighted and may drudge up old wounds</li>
        <li>It may just clarify the reasons you need to separate and/or divorce</li>
        <li>Both parties must be invested and willing to participate</li>
      </ul>
    </div>
  </section>

  <section class="option option--diy">
    <div class="option-head">
      <span class="option-num">option #3</span>
      <h2 class="option-name">Do it Yourself</h2>
    </div>
    <div class="pros">
      <h3 class="group-title">Advantages:</h3>
      <ul class="points">
        <li>No attorney fees</li>
        <li>You are your own attorney</li>
      </ul>
    </div>
    <div class="cons">
      <h3 class="group-title">Disadvantages:</h3>
      <ul class="points">
        <li>People often find that what is “fair,” may in fact, not be truly fair</li>
        <li>Often times, people do not know the risks</li>
        <li>Complicated legal system within intrigue rules</li>
        <li>Unsure how to complete the necessary paperwork and meet the deadlines</li>
      </ul>
    </div>
  </section>

  <section class="option option--limited">
    <div class="option-head">
      <span class="option-num">option #4</span>
      <h2 class="option-name">Limited<br>Representation</h2>
    </div>
    <div class="pros">
      <h3 class="group-title">Advantages:</h3>
      <ul class="points">
        <li>Balance between going alone and our limited involvement in the case</li>
      </ul>
    </div>
    <div class="cons">
      <h3 class="group-title">Disadvantages:</h3>
      <ul class="points">
        <li>Our terms may not benefit from our legal knowledge</li>
        <li>The legal consequences of your legal documents will not be explained to you so that you can formulate a plan for handling the rest of your case.</li>
        <li>Your spouse or other parties may cause your legal fees to increase significantly without action on your part</li>
      </ul>
    </div>
  </section>

  <section class="option option--hire">
    <div class="option-head">
      <span class="option-num">option #5</span>
      <h2 class="option-name">Hire Us</h2>
    </div>
    <div class="pros">
      <h3 class="group-title">Advantages:</h3>
      <ul class="points">
        <li>Gain the full benefits of our experience</li>
        <li>Have a team of Family Law focus attorneys</li>
        <li>Often saves you or makes you money in the long run</li>
        <li>Save you time, energy and stress</li>
      </ul>
    </div>
    <div class="cons">
      <h3 class="group-title">Disadvantages:</h3>
      <ul class="points">
        <li>Remain unhappy, depressed, anxious</li>
        <li>Money and assets may disappear</li>
        <li>What is going to change?</li>
      </ul>
    </div>
  </section>
</body>
</html>
```